Fresh mango cartoon design with atractive apparance

I need cartoon desgin for fresh alfonso mango imported from india i have my own logo but i need the cartoon desgin with a slogen name for the mango for example (tilvor) or( ronex )or any good name easy to remember with rethem i need it fancy notable click to any one sees the cartoon
The cartoon is rectangle the measurement are 36cm long by 26cm width by 8cm hight and the cartoon Weigh 260 grams empty
Ineed my company name and logo the cartoon color should rime with logo colors or something good with it

Not yet satisfied with what I got maybe because of short periods of time there for i want to get extra time so the designers have time to be more creative Thanks for all designers who submitted their design

Local fruit market and hapermarket in kuwait

Sans Serif

• Attracted design easy to remember and creative also must have the weight of the mango proximitly 3 kg . Grade Aproduct ,
• fance realaity pic of mango if possible. My company logo and insagram add.
• Not really

```html
<!DOCTYPE html>
<html lang="en">
<head>
<meta charset="utf-8">
<title>ronex – Fresh Tasty Mango</title>
<link rel="stylesheet" href="https://fonts.googleapis.com/css2?family=Open+Sans:wght@700&family=Oswald:wght@700&family=Cairo:wght@700&display=swap">
<style>
  :root {
    --frame-green: #34502a;
    --mango-orange: #ff5f03;
    --burst-white: #ffffff;
    --leaf-green: #35ae2d;
    --pill-green: #3aad3e;
    --brand-brown: #5e3a1a;
    --art-light: #fbb54a;
    --art-deep: #f39a2a;
  }
  * { margin: 0; padding: 0; box-sizing: border-box; }
  html, body { width: 1139px; height: 1200px; overflow: hidden; }
  body {
    background: var(--frame-green);
    position: relative;
    font-family: "Open Sans", sans-serif;
  }
  .carton-face {
    position: absolute;
    left: 68px; top: 42px;
    width: 993px; height: 773px;
    background: var(--mango-orange);
    overflow: hidden;
  }
  .burst {
    position: absolute;
    left: 0; top: 0;
    width: 993px; height: 773px;
  }
  .fruit-art {
    position: absolute;
    left: 317px; top: 80px;
    width: 290px; height: 295px;
    background: linear-gradient(160deg, var(--art-light), var(--art-deep));
  }
  .brand-name {
    position: absolute;
    left: 0; width: 993px;
    top: 403px;
    text-align: center;
    font-family: "Oswald", sans-serif;
    font-weight: 700;
    font-size: 210px;
    line-height: 1;
    color: var(--brand-brown);
  }
  .slogan-pill {
    position: absolute;
    left: 292px; top: 623px;
    width: 384px; height: 57px;
    border-radius: 29px;
    background: var(--pill-green);
    color: var(--burst-white);
    font-weight: 700;
    font-size: 32px;
    line-height: 57px;
    text-align: center;
  }
  .product-band {
    position: absolute;
    left: 68px; top: 815px;
    width: 993px; height: 110px;
    background: var(--leaf-green);
    color: var(--burst-white);
    font-weight: 700;
    font-size: 62px;
    line-height: 110px;
    padding-left: 85px;
    letter-spacing: 7px;
    white-space: nowrap;
  }
  .company-panel {
    position: absolute;
    left: 68px; top: 956px;
    width: 993px; height: 189px;
    background: var(--burst-white);
    display: flex;
    align-items: center;
    justify-content: center;
    gap: 18px;
  }
  .company-dot {
    width: 56px; height: 56px;
    border-radius: 50%;
    background: var(--pill-green);
  }
  .company-name {
    font-family: "Cairo", sans-serif;
    font-weight: 700;
    font-size: 64px;
    color: var(--brand-brown);
    direction: rtl;
  }
</style>
</head>
<body>
  <section class="carton-face">
    <svg class="burst" viewBox="0 0 993 773" aria-hidden="true">
      <g transform="translate(484 388)">
        <polygon fill="var(--burst-white)" points="0,-385 48,-306 119,-366 141,-276 226,-311 219,-219 311,-226 276,-141 366,-119 306,-48 385,0 306,48 366,119 276,141 311,226 219,219 226,311 141,276 119,366 48,306 0,385 -48,306 -119,366 -141,276 -226,311 -219,219 -311,226 -276,141 -366,119 -306,48 -385,0 -306,-48 -366,-119 -276,-141 -311,-226 -219,-219 -226,-311 -141,-276 -119,-366 -48,-306"/>
      </g>
    </svg>
    <div class="fruit-art" role="img" aria-label="Cartoon illustration of a ripe mango with a green leaf"></div>
    <h1 class="brand-name">ronex</h1>
    <p class="slogan-pill">Enjoy freshness</p>
  </section>

  <p class="product-band">FRESH TASTY MANGO</p>

  <footer class="company-panel">
    <span class="company-dot"></span>
    <span class="company-name">متجر بستاني</span>
  </footer>
</body>
</html>
```